CBD/HEMP website for e-commerce store

I need a CBD website for my shopify store. I am looking for a layout similar to these site ( https://quietmeadowcbd.com/ ) (https://elmridgecbd.com/) but with my logo and products. I am attaching what my logo looks like so that it helps with the design.

Target Market(s)

CBD HEMP CANNABIS

Industry/Entity Type

Cannabis

Coding

Coded - Design and coding required

Number of Pages Required

5+ page

Requirements
Nice to have
• I would like for it to have a trendy/galaxy feel

```html
<!DOCTYPE html>
<html lang="en">
<head>
<meta charset="utf-8">
<title>Starleaf — CBD &amp; Hemp Store</title>
<link rel="stylesheet" href="https://fonts.googleapis.com/css2?family=Poppins:wght@600;700&family=IBM+Plex+Sans:wght@400;600;700&display=swap">
<style>
:root{
  --space-deep:#0b0a1c;
  --space-mid:#171431;
  --nebula:#3a1f5e;
  --ink:#ffffff;
  --ink-soft:#d9d8e6;
  --accent:#f04a23;
  --card:#ffffff;
  --card-ink:#1d1d1d;
  --card-soft:#444;
}
*{margin:0;padding:0;box-sizing:border-box}
html,body{width:1200px;height:4237px;overflow:hidden}
body{
  position:relative;
  font-family:"IBM Plex Sans",sans-serif;
  color:var(--ink);
  background:
    radial-gradient(ellipse 420px 300px at 500px 1180px,rgba(98,44,140,.45),transparent 70%),
    radial-gradient(ellipse 500px 320px at 200px 3050px,rgba(70,40,120,.35),transparent 70%),
    radial-gradient(ellipse 500px 320px at 1000px 3600px,rgba(70,40,120,.3),transparent 70%),
    linear-gradient(180deg,var(--space-mid),var(--space-deep) 40%,var(--space-mid) 70%,var(--space-deep));
}
.abs{position:absolute}
.btn{position:absolute;background:var(--accent);color:#fff;font-weight:600;text-transform:uppercase;display:flex;align-items:center;justify-content:center;text-decoration:none}

/* header */
.site-header{position:absolute;left:0;top:0;width:1200px;height:115px;background:#0d0b1e}
.brand{position:absolute;left:140px;top:38px;display:flex;align-items:center;gap:12px;font-family:"Poppins",sans-serif;font-weight:700;font-size:30px;color:var(--ink)}
.brand-dot{width:22px;height:22px;border-radius:50%;background:var(--accent)}
.main-nav{position:absolute;left:562px;top:50px;display:flex;gap:33px;font-size:13px;letter-spacing:.3px}
.main-nav a{color:var(--ink);text-decoration:none}
.main-nav a.active{font-weight:700;text-decoration:underline;text-underline-offset:5px}
.cart{position:absolute;left:1025px;top:44px}
.cart-count{position:absolute;left:1050px;top:41px;width:15px;height:15px;border-radius:50%;background:var(--accent);font-size:9px;display:flex;align-items:center;justify-content:center;font-weight:700}

/* hero */
.hero{position:absolute;left:0;top:115px;width:1200px;height:646px;
  background:radial-gradient(ellipse 300px 200px at 900px 420px,#e9ecd6,transparent 70%),radial-gradient(ellipse 260px 180px at 470px 180px,#dfe3c2,transparent 70%),linear-gradient(135deg,#6f7a6e,#4d5a58 40%,#6b5a42 60%,#48545a)}
.hero-title{position:absolute;left:79px;top:340px;font-family:"Poppins",sans-serif;font-weight:700;font-size:40px}
.hero-sub{position:absolute;left:84px;top:403px;font-size:16px;line-height:21px;text-transform:uppercase}
.hero .btn{left:85px;top:357px;width:150px;height:46px;font-size:17px}
.slider-arrows{position:absolute;left:1106px;top:580px}

/* section titles */
.section-title{position:absolute;left:0;width:1200px;text-align:center;font-family:"Poppins",sans-serif;font-weight:600;font-size:24px}
.section-title::after{content:"";position:absolute;left:577px;top:46px;width:46px;height:2px;background:var(--ink)}

/* product cards */
.product-photo{position:absolute;background:var(--card)}
.product-photo i{position:absolute;inset:30px 60px;border-radius:50%;display:block}
.product-name{position:absolute;text-align:center;font-weight:700;font-size:14px;text-transform:uppercase}
.product-desc{position:absolute;text-align:center;font-size:12.5px;line-height:20px;color:var(--ink-soft)}
.products .btn{width:108px;height:37px;font-size:13px}

.rec-photo{position:absolute;top:1452px;width:223px;height:243px;background:var(--card)}
.rec-photo i{position:absolute;inset:40px 35px;border-radius:40%;display:block}
.rec-meta{position:absolute;top:1712px;font-size:11.5px;line-height:20px;text-transform:uppercase}
.rec-meta b{display:block;font-size:13px}

.promo{position:absolute;left:0;top:1841px;width:1200px;height:526px;background:radial-gradient(ellipse 500px 300px at 600px 260px,#243a1c,#0e170c 80%)}
.promo-text{position:absolute;left:0;top:190px;width:1200px;text-align:center;font-family:"Poppins",sans-serif;font-weight:700;font-size:46px;line-height:54px;text-transform:uppercase}

.testimonial{position:absolute;left:327px;top:2522px;width:546px;text-align:center;font-size:15px;line-height:22.5px;color:var(--ink-soft)}
.testimonial-author{position:absolute;left:0;top:2670px;width:1200px;text-align:center;font-weight:700;font-size:14px}

.seller-card{position:absolute;top:2869px;width:300px;height:406px;background:var(--card);color:var(--card-ink);text-align:center}
.seller-card i{position:absolute;left:70px;top:25px;width:160px;height:190px;border-radius:45%;display:block}
.seller-card h3{position:absolute;left:0;top:246px;width:100%;font-size:14px;font-weight:700}
.seller-card p{position:absolute;left:20px;top:280px;width:260px;font-size:12.5px;line-height:20px;color:var(--card-soft)}
.seller-card .btn{left:92px;top:345px;width:116px;height:35px;font-size:13px}

.blog-card{position:absolute;top:3439px;width:289px;height:410px;background:var(--card);color:var(--card-ink)}
.blog-card .blog-photo{height:222px}
.blog-card h3{position:absolute;left:25px;top:245px;font-size:14px;font-weight:700;text-transform:uppercase}
.blog-card p{position:absolute;left:25px;top:278px;width:240px;font-size:12.5px;line-height:18px;color:var(--card-soft)}
.blog-card a{position:absolute;left:25px;top:363px;font-size:11px;font-weight:700;color:var(--accent);text-transform:uppercase}

.site-footer h4{position:absolute;top:3958px;font-size:14px;font-weight:700}
.footer-about{position:absolute;left:133px;top:3996px;width:280px;font-size:12.5px;line-height:21px;color:var(--ink-soft)}
.footer-menu{position:absolute;left:498px;top:3990px;list-style:none;font-size:12.5px;line-height:21px;text-transform:uppercase;color:var(--ink-soft)}
.footer-join{position:absolute;left:723px;top:3990px;font-size:12.5px;color:var(--ink-soft)}
.newsletter{position:absolute;left:725px;top:4034px;width:293px;height:46px;border:1.5px solid #fff;font-size:11px;padding:14px 18px;color:var(--ink-soft)}
.newsletter-go{position:absolute;left:1018px;top:4034px;width:47px;height:46px;background:var(--accent);display:flex;align-items:center;justify-content:center}
.footer-rule{position:absolute;left:133px;top:4135px;width:932px;height:1px;background:rgba(255,255,255,.12)}
.copyright{position:absolute;left:0;top:4176px;width:1200px;text-align:center;font-size:11px;color:var(--ink-soft)}
</style>
</head>
<body>

<header class="site-header">
  <div class="brand"><span class="brand-dot"></span>Starleaf</div>
  <nav class="main-nav">
    <a class="active" href="#">HOME</a><a href="#">ABOUT US</a><a href="#">PRODUCTS</a><a href="#">BLOG</a><a href="#">CONTACT US</a>
  </nav>
  <svg class="cart" width="30" height="28" viewBox="0 0 30 28" fill="none" stroke="#fff" stroke-width="2"><path d="M1 3h5l4 15h15l3-11H8"/><circle cx="12" cy="24" r="2"/><circle cx="23" cy="24" r="2"/></svg>
  <span class="cart-count">0</span>
</header>

<section class="hero" role="img" aria-label="Jars of hemp cream with a cannabis leaf on a woven tray">
  <h1 class="hero-title" style="top:225px">HEMP</h1>
  <p class="hero-sub" style="top:288px">Lorem ipsum is simply<br>dummy text of the printing</p>
  <a class="btn" href="#">Shop Now</a>
  <svg class="slider-arrows" width="36" height="20" viewBox="0 0 36 20" fill="none" stroke="#fff" stroke-width="2"><path d="M8 3 2 10l6 7M28 3l6 7-6 7"/></svg>
</section>

<section class="products">
  <h2 class="section-title" style="top:815px">OUR PRODUCTS</h2>
  <div class="product-photo" style="left:132px;top:898px;width:300px;height:226px" role="img" aria-label="Bowl of green hemp powder"><i style="background:radial-gradient(#a8b27a,#b06a3a 75%);inset:30px 78px"></i></div>
  <div class="product-photo" style="left:450px;top:898px;width:300px;height:226px" role="img" aria-label="CBD oil bottle with dried buds"><i style="background:radial-gradient(#6b4a2a,#8a8d6a 70%,#fff 72%)"></i></div>
  <div class="product-photo" style="left:771px;top:898px;width:301px;height:226px" role="img" aria-label="Three CBD oil dropper bottles"><i style="background:linear-gradient(90deg,#3b1f14,#5a2c18,#8a4a22);inset:35px 75px;border-radius:8px"></i></div>
  <h3 class="product-name" style="left:132px;top:1152px;width:300px">Lorem Ipsum</h3>
  <h3 class="product-name" style="left:450px;top:1152px;width:300px">Lorem Ipsum</h3>
  <h3 class="product-name" style="left:771px;top:1152px;width:301px">Lorem Ipsum</h3>
  <p class="product-desc" style="left:142px;top:1187px;width:280px">Lorem Ipsum is simply dummy text of the printing and typesetting industry.</p>
  <p class="product-desc" style="left:460px;top:1187px;width:280px">Lorem Ipsum is simply dummy text of the printing and typesetting industry.</p>
  <p class="product-desc" style="left:781px;top:1187px;width:280px">Lorem Ipsum is simply dummy text of the printing and typesetting industry.</p>
  <a class="btn" href="#" style="left:231px;top:1249px">Shop Now</a>
  <a class="btn" href="#" style="left:545px;top:1249px">Shop Now</a>
  <a class="btn" href="#" style="left:868px;top:1249px">Shop Now</a>
</section>

<section class="recommended">
  <h2 class="section-title" style="top:1363px">RECOMMENDED FOR YOU</h2>
  <div class="rec-photo" style="left:132px" role="img" aria-label="Hemp cookies with a cannabis leaf"><i style="background:radial-gradient(#c98a4a,#7a4a24 70%)"></i></div>
  <div class="rec-photo" style="left:376px" role="img" aria-label="Glass jar of hemp butter"><i style="background:radial-gradient(#efe2b4,#c8b47a 75%)"></i></div>
  <div class="rec-photo" style="left:612px" role="img" aria-label="CBD oil bottle with dropper"><i style="background:linear-gradient(#d9a32a,#7a5a1a);inset:60px 80px;border-radius:10px"></i></div>
  <div class="rec-photo" style="left:847px" role="img" aria-label="Bowl of hemp treats"><i style="background:radial-gradient(#6a3a1c,#3b2212 70%)"></i></div>
  <p class="rec-meta" style="left:133px">Lorem ipsum is simply<b>$25.00</b></p>
  <p class="rec-meta" style="left:377px">Lorem ipsum is simply<b>$25.00</b></p>
  <p class="rec-meta" style="left:613px">Lorem ipsum is simply<b>$25.00</b></p>
  <p class="rec-meta" style="left:848px">Lorem ipsum is simply<b>$25.00</b></p>
</section>

<section class="promo" role="img" aria-label="Dark close-up of cannabis leaves">
  <p class="promo-text">10% Off<br>New Products</p>
</section>

<section class="testimonials">
  <h2 class="section-title" style="top:2439px">TESTIMONIALS</h2>
  <p class="testimonial">At vero eos et accusamus et iusto odio dignissimos ducimus qui blanditiis praesentium voluptatum deleniti atque corrupti quos dolores et quas molestias excepturi sint occaecati cupiditate non provident, similique sunt in culpa qui officia deserunt mollitia animi, id est laborum et dolorum fuga. Et harum quidem rerum facilis est et expedita</p>
  <p class="testimonial-author">RICHARD</p>
</section>

<section class="best-sellers">
  <h2 class="section-title" style="top:2772px">BEST SELLERS</h2>
  <article class="seller-card" style="left:132px"><i role="img" aria-label="Bottle of hemp seed oil" style="background:radial-gradient(#f2d44a,#c99a1a 70%)"></i><h3>LOREM IPSUM IS SIMPLY</h3><p>Lorem Ipsum is simply dummy text of the printing and typesetting industry.</p><a class="btn" href="#">Shop Now</a></article>
  <article class="seller-card" style="left:450px"><i role="img" aria-label="Chocolate pieces with a cannabis leaf" style="background:radial-gradient(#5a9a2a,#4a2418 70%)"></i><h3>LOREM IPSUM IS SIMPLY</h3><p>Lorem Ipsum is simply dummy text of the printing and typesetting industry.</p><a class="btn" href="#">Shop Now</a></article>
  <article class="seller-card" style="left:771px;width:301px"><i role="img" aria-label="Heart-shaped hemp treats with a leaf" style="background:radial-gradient(#4a8a2a,#e2693a 65%)"></i><h3>LOREM IPSUM IS SIMPLY</h3><p>Lorem Ipsum is simply dummy text of the printing and typesetting industry.</p><a class="btn" href="#">Shop Now</a></article>
</section>

<section class="blog">
  <h2 class="section-title" style="top:3350px">LATEST BLOG</h2>
  <article class="blog-card" style="left:133px"><div class="blog-photo" role="img" aria-label="Dropper above an oil bottle among green leaves" style="background:radial-gradient(#7ab04a,#2a4a1a 80%)"></div><h3>Lorem ipsum dolor sit</h3><p>Lorem Ipsum is simply dummy texte printing and typesetting industry. quasi architecto beatae vitae dicta explicabo. Nemo enim ipsam</p><a href="#">Read More</a></article>
  <article class="blog-card" style="left:455px;width:290px"><div class="blog-photo" role="img" aria-label="Tins of hemp balm with a leaf" style="background:radial-gradient(#e8c98a,#2a9a9a 80%)"></div><h3>Lorem ipsum dolor sit</h3><p>Lorem Ipsum is simply dummy texte printing and typesetting industry. quasi architecto beatae vitae dicta explicabo. Nemo enim ipsam</p><a href="#">Read More</a></article>
  <article class="blog-card" style="left:776px"><div class="blog-photo" role="img" aria-label="Hemp seeds, flour and oil on a table" style="background:radial-gradient(#b8a060,#4a3a22 80%)"></div><h3>Lorem ipsum dolor sit</h3><p>Lorem Ipsum is simply dummy texte printing and typesetting industry. quasi architecto beatae vitae dicta explicabo. Nemo enim ipsam</p><a href="#">Read More</a></article>
</section>

<footer class="site-footer">
  <h4 style="left:133px">ABOUT</h4>
  <p class="footer-about">Lorem Ipsum is simply dummy text of the printing and typesetting industry. veritatis et qai architecto beatae vitae dicta sunt explicabo. Nemo enim ipsam</p>
  <h4 style="left:498px">MENU</h4>
  <ul class="footer-menu"><li>Home</li><li>Pricing</li><li>How it works</li><li>Gift boxes</li><li>Contact us</li></ul>
  <h4 style="left:723px">STAY CONNECTED</h4>
  <p class="footer-join">Join our mailing list to get updates</p>
  <div class="newsletter">E mail address</div>
  <div class="newsletter-go"><svg width="12" height="16" viewBox="0 0 12 16" fill="none" stroke="#fff" stroke-width="2"><path d="M3 2l6 6-6 6"/></svg></div>
  <div class="footer-rule"></div>
  <p class="copyright">Copyright © 2020 All Rights Reserved</p>
</footer>

</body>
</html>
```